Marlow Advisory Education services needs a banner design

We need a banner for our Australian company called Marlow Advisory. Banners are 76cm wide and from 122 - 244cm in length. We are an innovative educational leadership search and development company that is also providing future foresight strategy planning for schools. We want to communicate that we are assisting schools to co-create their 21st century learning environment and providing the change-maker leaders to action the innovative programs in schools. Words that sum up our company are collaborative, creative, connecting, communicators, relational, transformational. We already have a business card and stationery.
Industry/Entity Type
Education
Look and feel

```html
<!DOCTYPE html>
<html lang="en">
<head>
<meta charset="utf-8">
<title>Marlow Advisory – Banner</title>
<link rel="stylesheet" href="https://fonts.googleapis.com/css2?family=Figtree:wght@500;600&family=Roboto+Condensed:wght@700&family=Roboto:wght@400&family=Libre+Baskerville:ital,wght@0,700;1,400&display=swap">
<style>
  :root {
    --purple: #522d7f;
    --purple-text: #4e2b7c;
    --green: #5d8a3a;
    --green-light: #a9d08f;
    --white: #ffffff;
    --photo-a: #c9cdc4;
    --photo-b: #e8e6e1;
  }
  * { margin: 0; padding: 0; box-sizing: border-box; }
  html, body { width: 1200px; height: 2892px; overflow: hidden; background: var(--white); }
  .banner {
    position: relative;
    width: 1200px;
    height: 2892px;
    overflow: hidden;
    background: linear-gradient(180deg, var(--green-light) 0px, #dcebd1 560px, var(--white) 1080px);
  }
  .brand {
    position: absolute;
    left: 140px;
    top: 190px;
    display: flex;
    align-items: center;
    gap: 28px;
  }
  .brand-dot {
    width: 70px; height: 70px;
    border-radius: 50%;
    background: var(--green);
  }
  .brand-name {
    font-family: "Figtree", sans-serif;
    font-weight: 600;
    font-size: 84px;
    line-height: 1;
    color: var(--purple-text);
  }
  .tagline {
    position: absolute;
    left: 407px;
    top: 322px;
    font-family: "Libre Baskerville", serif;
    font-style: italic;
    font-size: 38px;
    color: var(--purple-text);
  }
  .mission {
    position: absolute;
    left: 0; right: 0;
    top: 612px;
    text-align: center;
    font-family: "Figtree", sans-serif;
    font-weight: 500;
    font-size: 60px;
    line-height: 79.5px;
    color: var(--purple-text);
  }
  .photo {
    position: absolute;
    left: 0; top: 1167px;
    width: 1200px; height: 1000px;
    background: linear-gradient(135deg, var(--photo-a) 0%, var(--photo-b) 55%, #d7dcd2 100%);
  }
  .wave {
    position: absolute;
    left: 0; top: 0;
    width: 1200px; height: 2892px;
  }
  .values {
    position: absolute;
    inset: 0;
    color: var(--white);
  }
  .value {
    position: absolute;
    line-height: 1;
    font-family: "Roboto Condensed", sans-serif;
    font-weight: 700;
    white-space: nowrap;
  }
  .value--transformational { left: 328px; top: 2215px; font-size: 46px; }
  .value--creative { left: 72px; top: 2335px; font-size: 52px; }
  .value--connecting { left: 403px; top: 2356px; font-size: 50px; font-family: "Roboto", sans-serif; font-weight: 400; }
  .value--relational { left: 828px; top: 2299px; font-size: 54px; }
  .value--collaborative { left: 173px; top: 2488px; font-size: 36px; }
  .value--communicating { left: 688px; top: 2455px; font-size: 48px; }
  .web {
    position: absolute;
    left: 0; right: 0;
    top: 2733px;
    display: flex;
    justify-content: center;
    align-items: center;
    gap: 20px;
    font-family: "Libre Baskerville", serif;
    font-weight: 700;
    font-size: 52px;
    color: var(--white);
  }
  .web-icon { width: 34px; height: 34px; }
  .web-accent { color: #7fb04e; }
</style>
</head>
<body>
<main class="banner">
  <header>
    <div class="brand">
      <span class="brand-dot"></span>
      <span class="brand-name">Marlow Advisory</span>
    </div>
    <p class="tagline">Re-imagining Education</p>
  </header>

  <p class="mission">We are assisting schools to<br>co-create their 21st century<br>learning environment and<br>providing the transformational<br>leaders to action innovation.</p>

  <div class="photo" role="img" aria-label="Photo of a smiling young professional woman holding a tablet, with colleagues meeting at a table behind her"></div>

  <svg class="wave" viewBox="0 0 1200 2892" aria-hidden="true">
    <path d="M0 1990 C 220 2130, 520 2120, 820 1990 S 1120 1855 1200 1845 L1200 2892 L0 2892 Z" fill="#ffffff"/>
    <path d="M0 2030 C 220 2160, 520 2140, 820 2010 S 1120 1880 1200 1872 L1200 2892 L0 2892 Z" fill="#5d8a3a"/>
    <path d="M0 2044 C 230 2172, 530 2150, 830 2022 S 1130 1894 1200 1888 L1200 2892 L0 2892 Z" fill="#ffffff"/>
    <path d="M0 2052 C 230 2180, 530 2160, 830 2032 S 1130 1906 1200 1900 L1200 2892 L0 2892 Z" fill="#522d7f"/>
    <ellipse cx="1160" cy="1893" rx="12" ry="7" fill="#5d8a3a"/>
  </svg>

  <section class="values">
    <span class="value value--transformational">TRANSFORMATIONAL</span>
    <span class="value value--creative">CREATIVE</span>
    <span class="value value--connecting">CONNECTING</span>
    <span class="value value--relational">RELATIONAL</span>
    <span class="value value--collaborative">COLLABORATIVE</span>
    <span class="value value--communicating">COMMUNICATING</span>
  </section>

  <footer class="web">
    <svg class="web-icon" viewBox="0 0 34 34" aria-hidden="true">
      <g fill="none" stroke="#ffffff" stroke-width="2">
        <circle cx="17" cy="17" r="15"/>
        <ellipse cx="17" cy="17" rx="7" ry="15"/>
        <line x1="2" y1="17" x2="32" y2="17"/>
        <line x1="17" y1="2" x2="17" y2="32"/>
        <path d="M5 9 H29 M5 25 H29"/>
      </g>
    </svg>
    <span>www.<span class="web-accent">marlow</span>.education</span>
  </footer>
</main>
</body>
</html>
```